Business card for law firm

Need business card for new law firm. Think confident, authoritative, conservative, but not stuffy or old-fashioned.

Contact Information for Business Card

Content for card - logo (uploaded), plus the following:

Paul Whitcombe (larger font)
Managing Partner (larger font, but not as large as name)
Level 9, 7 Ferris Lane
Sydney NSW 2000
Main Tel 02 9364 2710
Direct Tel 02 8472 3159
Email paul@qvlegal.com.au
www.qvlegal.com.au

Letterhead design should include logo plus:
Level 9, 7 Ferris Lane
Sydney NSW 2000
Tel 02 8472 3159
www.qvlegal.com.au

```html
<!DOCTYPE html>
<html lang="en">
<head>
<meta charset="utf-8">
<title>Quayview Legal — Letterhead</title>
<link href="https://fonts.googleapis.com/css2?family=Questrial&family=Roboto:wght@400&display=swap" rel="stylesheet">
<style>
  :root {
    --backdrop: #e6e7e9;
    --paper: #f4f4f5;
    --navy: #0c1d4f;
    --ink: #6e6e70;
    --ink-soft: #8a8a8c;
    --signature-ink: #c9d6ea;
    --white: #ffffff;
  }
  * { margin: 0; padding: 0; box-sizing: border-box; }
  html, body {
    width: 1024px;
    height: 1200px;
    overflow: hidden;
    background: var(--backdrop);
  }
  .letterhead {
    position: absolute;
    left: 116px;
    top: 40px;
    width: 792px;
    height: 1120px;
    background: var(--paper);
    font-family: "Questrial", sans-serif;
    color: var(--ink);
  }
  .brand {
    position: absolute;
    top: 74px;
    left: 0;
    width: 100%;
    text-align: center;
  }
  .brand-square {
    display: block;
    width: 36px;
    height: 36px;
    margin: 0 auto 16px;
    background: var(--navy);
  }
  .brand-name {
    font-family: "Questrial", sans-serif;
    font-size: 26px;
    letter-spacing: 2px;
    color: var(--navy);
    text-transform: uppercase;
  }
  .letter {
    position: absolute;
    left: 74px;
    top: 292px;
    width: 658px;
  }
  .salutation {
    font-size: 19px;
    color: var(--ink-soft);
    margin-bottom: 36px;
  }
  .body-copy p {
    font-size: 11.3px;
    line-height: 14px;
    text-align: justify;
    margin-bottom: 14px;
  }
  .closing {
    font-size: 11.3px;
    margin-top: 28px;
  }
  .signature {
    display: block;
    margin-top: 50px;
    width: 140px;
    height: 58px;
    background: var(--signature-ink);
    border-radius: 4px;
  }
  .footer-band {
    position: absolute;
    left: 0;
    top: 1059px;
    width: 100%;
    height: 28px;
    background: var(--navy);
    color: var(--white);
    font-family: "Roboto", sans-serif;
    font-size: 14px;
    line-height: 28px;
    text-align: center;
    padding-left: 40px;
  }
</style>
</head>
<body>
  <main class="letterhead">
    <header class="brand">
      <span class="brand-square"></span>
      <div class="brand-name">Quayview Legal</div>
    </header>

    <section class="letter">
      <p class="salutation">Dear Mr. Hartley,</p>
      <div class="body-copy">
        <p>Lorem ipsum dolor sit amet, consectetur adipiscing elit. Donec orci purus, luctus vitae dignissim eu, iaculis sed purus. Vivamus faucibus, ipsum nec aliquet viverra, leo mauris condimentum ligula, sit amet sagittis enim ligula quis arcu. Nam egestas tortor id nisi porttitor mattis. In tortor ante, ultricies in suscipit a, tempus non massa. Vivamus et auctor mi. Fusce vel massa nulla. Phasellus nec eros mauris, et scelerisque orci.</p>
        <p>Donec malesuada orci vitae nulla accumsan porta a id massa. Quisque accumsan iaculis magna sit amet fringilla. Maecenas consequat, magna eget tincidunt semper, odio nibh rutrum mi, id feugiat ante nisi eu risus. Vestibulum nunc orci, rhoncus a placerat in, ultricies in mi. Cras mattis varius eros, vel fringilla nisi suscipit eget. Quisque scelerisque sagittis nulla at porttitor.</p>
        <p>Sed id augue vitae urna euismod commodo aliquet a quam. Pellentesque arcu velit, cursus et malesuada ut, consequat et diam. Nullam erat sem, rhoncus id ullamcorper vitae, rhoncus et arcu. In ultricies ultricies nulla, ut rutrum nisi iaculis at. Donec eu magna a metus ornare faucibus. Fusce aliquet faucibus ultricies. Morbi semper, est id tincidunt gravida, sem arcu adipiscing lacus, ac bibendum nulla leo eu purus. Quisque nec diam sed risus consectetur a ccumsan quis quis nibh. Vestibulum id purus lorem.</p>
        <p>It is a long established fact that a reader will be distracted by the readable content of a page when looking at its layout. The point of using Lorem Ipsum is that it has a more-or-less normal distribution of letters, as opposed to using 'Content here, content here', making it look like readable English. Many desktop publishing packages</p>
      </div>
      <p class="closing">Sincerely,</p>
      <span class="signature" role="img" aria-label="Handwritten signature of Owen Hartley"></span>
    </section>

    <footer class="footer-band">Level 9, 7 Ferris Lane, Sydney NSW 2000 | 02 8472 3159 | www.qvlegal.com.au</footer>
  </main>
</body>
</html>
```